Letter head for peronal trainer

Letter head top and bottom. Elite looking design that looks modern and prestigious for high end clients. Black, silver, reds etc. Attached are my business cards (2 x pdfs) and my website is: www.doriankemble.net for style/ideas

Needs to look good when printing and be locked onto the page when people use my word docs on the computer, I don't want it to be 'clickable' if you know what I mean. Needs to work in A4 in portrait (and in landscape, for programme cards). I need it to be editable for when I adjust the text myself. Needs my contact details and social media details and title personal trainer (Central London/Greenwich/Blackheath) and Online Distance Coaching. . A little picture at the bottom too if it works (Like the vest one)

```html
<!DOCTYPE html>
<html lang="en">
<head>
<meta charset="utf-8">
<title>Dorian Kemble – Letterhead</title>
<link href="https://fonts.googleapis.com/css2?family=Oswald:wght@600;700&family=Arimo:wght@400;700&display=swap" rel="stylesheet">
<style>
  :root {
    --ink: #000000;
    --charcoal: #231f20;
    --steel: #5f5f5f;
    --silver: #d4d4d4;
    --paper: #ffffff;
    --text: #222222;
  }
  * { margin: 0; padding: 0; box-sizing: border-box; }
  html, body { width: 927px; height: 1200px; overflow: hidden; background: var(--paper); }
  .letterhead { position: relative; width: 927px; height: 1200px; background: var(--paper); overflow: hidden; font-family: "Arimo", Arial, sans-serif; color: var(--text); }

  .header-wave { position: absolute; left: 0; top: 0; width: 927px; height: 290px; }

  .header-title { position: absolute; right: 48px; top: 32px; text-align: right; color: var(--paper); }
  .header-title .name { font-family: "Oswald", "Arial Narrow", sans-serif; font-weight: 700; font-size: 34px; line-height: 1; letter-spacing: 0.2px; }
  .header-title .role { font-weight: 700; font-size: 14px; letter-spacing: 2.6px; line-height: 1; margin-top: 6px; }
  .header-title .service { font-weight: 700; font-size: 14px; letter-spacing: 0.3px; line-height: 1; margin-top: 3px; }

  .footer-photo { position: absolute; left: 0; top: 977px; width: 134px; height: 192px;
    background: linear-gradient(160deg, #cfcfcf 0%, #8a8a8a 45%, #bdbdbd 100%);
    clip-path: polygon(40% 0, 65% 4%, 80% 30%, 100% 80%, 100% 100%, 0 100%, 0 35%, 22% 20%); }

  .footer-brand { position: absolute; left: 550px; top: 1062px; font-family: "Oswald", "Arial Narrow", sans-serif; font-weight: 700; font-size: 42px; line-height: 0.92; letter-spacing: -0.5px; transform: scaleX(0.88); transform-origin: left top; }
  .footer-brand .first { color: var(--charcoal); display: block; }
  .footer-brand .last { color: var(--steel); display: block; }

  .footer-tagline { position: absolute; left: 688px; top: 1074px; font-size: 8.5px; line-height: 13px; color: var(--text); white-space: nowrap; }

  .footer-frame { position: absolute; left: 673px; top: 1101px; width: 214px; height: 67px; border-top: 1px solid var(--steel); border-right: 1px solid var(--steel); }
  .footer-rule { position: absolute; left: 0; top: 1168px; width: 887px; border-top: 1px solid var(--steel); }

  .contact-row { position: absolute; top: 1151px; left: 0; width: 927px; font-size: 11px; }
  .contact { position: absolute; display: flex; align-items: center; gap: 5px; white-space: nowrap; }
  .contact svg { display: block; }
  .contact.phone { left: 334px; font-size: 12px; top: 1px; }
  .contact.email { left: 460px; }
  .contact.web { left: 639px; }
  .contact.social { left: 805px; }

  .footer-band { position: absolute; left: 0; top: 1174px; width: 927px; height: 26px; background: var(--charcoal); }
</style>
</head>
<body>
<main class="letterhead">
  <svg class="header-wave" viewBox="0 0 927 290">
    <defs>
      <linearGradient id="silverSweep" x1="0" y1="0" x2="1" y2="0">
        <stop offset="0" stop-color="#bdbdbd"/>
        <stop offset="0.35" stop-color="#f2f2f2"/>
        <stop offset="1" stop-color="#ffffff"/>
      </linearGradient>
      <linearGradient id="silverRight" x1="0" y1="0" x2="1" y2="0">
        <stop offset="0" stop-color="#ffffff"/>
        <stop offset="0.5" stop-color="#d9d9d9"/>
        <stop offset="1" stop-color="#ffffff"/>
      </linearGradient>
      <linearGradient id="portraitTone" x1="0" y1="0" x2="1" y2="1">
        <stop offset="0" stop-color="#3a3a3a"/>
        <stop offset="0.5" stop-color="#8c8c8c"/>
        <stop offset="1" stop-color="#4a4a4a"/>
      </linearGradient>
    </defs>
    <path d="M0 190 C60 250 130 290 240 260 C330 236 300 220 340 205 C120 240 60 230 0 200 Z" fill="url(#silverSweep)"/>
    <path d="M330 190 C480 130 640 120 927 210 L927 205 C700 135 520 140 330 185 Z" fill="url(#silverRight)"/>
    <path d="M0 0 H927 V210 C780 140 640 115 520 140 C380 165 300 215 170 220 C90 222 40 200 0 178 Z" fill="var(--ink)"/>
    <path role="img" aria-label="Black and white photo of the trainer, bare-chested, upper body" d="M0 0 H160 C175 60 180 140 178 218 C120 222 60 205 0 178 Z" fill="url(#portraitTone)"/>
  </svg>

  <header class="header-title">
    <div class="name">DORIAN KEMBLE</div>
    <div class="role">PERSONAL TRAINER</div>
    <div class="service">ONLINE DISTANCE COACHING</div>
  </header>

  <div class="footer-photo" role="img" aria-label="Black and white photo of the trainer in a vest lifting dumbbells"></div>

  <div class="footer-brand"><span class="first">DORIAN</span><span class="last">KEMBLE</span></div>
  <div class="footer-tagline">Ex Pro Athlete &amp; Forces Officer<br>Fitness Model &amp; Physique Competitor</div>
  <div class="footer-frame"></div>

  <div class="contact-row">
    <span class="contact phone">
      <svg width="8" height="12" viewBox="0 0 8 12"><path d="M2 0 L4 0.5 L3.5 3.5 L2.5 4 C2.6 6 3.2 8 4.5 9 L5.5 8.5 L7.5 10.5 L6 12 C2 11 0 6 0.5 1.5 Z" fill="#222"/></svg>
      07700900418
    </span>
    <span class="contact email">
      <svg width="11" height="11" viewBox="0 0 11 11"><circle cx="5.5" cy="5.5" r="4.6" fill="none" stroke="#222" stroke-width="1.2"/><path d="M1 5.5 H10 M5.5 1 V10" stroke="#222" stroke-width="0.8"/></svg>
      kemble.dorianPT@postbox.net
    </span>
    <span class="contact web">
      <svg width="12" height="8" viewBox="0 0 12 8"><rect width="12" height="8" fill="#222"/><path d="M0 0 L6 4.5 L12 0" stroke="#fff" stroke-width="1" fill="none"/></svg>
      www.doriankemble.net
    </span>
    <span class="contact social">
      <svg width="10" height="10" viewBox="0 0 10 10"><circle cx="5" cy="5" r="5" fill="#222"/></svg>
      @kembly_29
    </span>
  </div>

  <div class="footer-rule"></div>
  <div class="footer-band"></div>
</main>
</body>
</html>
```